Spring Detox sale graphics for social media

You MUST read the Brief in the WORD document and follow the instructions there. I want to create 10 social media graphics (new Instagram size 4:5 (1080 x 1350 pixels) focusing on our Mother’s Day Spring Detox Sale graphics, using any of the pics attached. Use the attached pics, NO RANDOM STOCK PHOTOGRAPHY. For the color scheme of the graphics, they should all be complementary to the product colors or feel like Spring time.

Target Market(s)

primarily women

Requirements
Must have
• the photos and text attached

```html
<!DOCTYPE html>
<html lang="en">
<head>
<meta charset="utf-8">
<title>Mother's Day Spring Detox Sale – Social Set</title>
<link rel="stylesheet" href="https://fonts.googleapis.com/css2?family=Antonio:wght@200;400;600;700&family=Anton&display=swap">
<style>
:root{
  --canvas:#0f0f0f;
  --white:#ffffff;
  --ink:#262626;
  --forest:#2c5d4d;
  --forest-deep:#1e4639;
  --teal:#3e9a80;
  --mint:#4fd3b0;
  --lilac:#c47ccb;
  --orchid:#9a4aa0;
  --pink-hot:#f48ae6;
  --royal:#2f4fc2;
  --sky:#3f66e0;
  --sun:#f6b81a;
  --crimson:#b8232c;
  --rose:#c8609e;
  --plum:#993a70;
  --indigo:#3b2f73;
  --indigo-deep:#27215a;
  --navy-text:#37307a;
  --sage:#5fae8e;
  --green-band:#2f6d57;
  --maroon:#7a2a56;
  --photo-warm:#8a6a55;
  --photo-light:#e4e1dc;
}
*{margin:0;padding:0;box-sizing:border-box}
html,body{width:1200px;height:3119px;overflow:hidden;background:var(--canvas)}
body{position:relative;font-family:'Antonio',sans-serif;color:var(--white)}
.tile{position:absolute;width:461px;height:575px;overflow:hidden}
.col-a{left:127px}.col-b{left:613px}
.row-1{top:81px}.row-2{top:674px}.row-3{top:1268px}.row-4{top:1865px}.row-5{top:2462px}
.line{position:absolute;white-space:nowrap;line-height:1;text-transform:uppercase;font-weight:700}
.center{left:0;width:461px;text-align:center}
.heavy{font-family:'Anton',sans-serif;font-weight:400}
.light{font-weight:200}
.vert{position:absolute;transform:rotate(-90deg);transform-origin:left top;white-space:nowrap;line-height:1;text-transform:uppercase;font-weight:700}
.photo{position:absolute}
.box{position:absolute}
svg.shape{position:absolute;left:0;top:0}

.t1{background:var(--forest)}
.t1 .photo{left:0;top:215px;width:461px;height:360px;background:linear-gradient(180deg,#3a6658 0%,#d9d9d6 38%,#ecebe8 100%)}
.t1 .badge{left:18px;top:115px;width:424px;height:68px;background:var(--teal);border-radius:8px}
.t1 .pill{left:34px;top:483px;width:393px;height:70px;background:var(--forest-deep);border-radius:10px}

.t2 .photo{inset:0;background:linear-gradient(90deg,var(--orchid) 0%,#a562a8 30%,#8c6a66 55%,var(--photo-warm) 80%,#c9c2bc 100%)}
.t2 .tab{left:0;top:0;width:298px;height:122px;background:var(--lilac);border-radius:0 0 10px 0}

.t3 .photo{inset:0;background:linear-gradient(90deg,var(--royal) 0%,#3552b0 35%,#7a6a75 62%,var(--photo-warm) 80%,#cfc8c1 100%)}

.t4{background:var(--photo-light)}
.t4 .rule{position:absolute;top:470px;height:3px;background:var(--ink)}

.t5 .photo{inset:0;background:linear-gradient(180deg,#3c5e52,#36574b 60%,#4a6a5e)}
.t5 .badge{left:60px;top:45px;width:340px;height:103px;background:var(--teal);border-radius:10px}

.t6{background:var(--rose)}
.t6 .frame{left:35px;top:283px;width:390px;height:155px;background:var(--plum);border-radius:10px;border-bottom:4px solid var(--white)}

.t7{background:var(--indigo)}
.t7 .frame{left:91px;top:321px;width:278px;height:133px;background:var(--indigo-deep);border-radius:8px}

.t8 .photo{left:0;top:125px;width:461px;height:450px;background:linear-gradient(90deg,#86c6aa 0%,var(--sage) 30%,#7b7a6c 60%,var(--photo-warm) 80%,#d3ccc4 100%)}
.t8 .band{left:0;top:0;width:461px;height:125px;background:var(--green-band)}
.t8 .frame{left:27px;top:285px;width:156px;height:79px;background:var(--green-band);border-radius:6px}
.t8 .dark{color:#1d2a25}

.t9 .photo{inset:0;background:linear-gradient(270deg,var(--crimson) 0%,#b02a30 38%,#8a5a52 60%,var(--photo-warm) 78%,#d8d1ca 100%)}
.t9 .frame{left:257px;top:203px;width:204px;height:87px;background:var(--white);border-radius:8px 0 0 8px}
.t9 .line{right:28px;text-align:right}

.t10{background:var(--white)}
.t10 .photo{left:84px;top:312px;width:133px;height:260px;background:linear-gradient(180deg,#d8cfc8,#b9a9a0 50%,#efeae6);border-radius:6px}
.t10 .line{right:26px;text-align:right}
</style>
</head>
<body>

<section class="tile t1 col-a row-1">
  <div class="photo" role="img" aria-label="Group of four supplement bottles on a light surface"></div>
  <div class="line center" style="top:32px;font-size:78px">Mother’s Day</div>
  <div class="box badge"></div>
  <div class="line center" style="top:121px;font-size:56px">Spring Detox Sale</div>
  <div class="box pill"></div>
  <div class="line" style="left:34px;width:393px;text-align:center;top:496px;font-size:44px"><span style="color:var(--mint)">25% Off</span> Everything!</div>
</section>

<section class="tile t2 col-b row-1">
  <div class="photo" role="img" aria-label="Smiling woman in a white sweater standing in a kitchen behind a row of supplement bottles"></div>
  <div class="box tab"></div>
  <div class="line" style="left:27px;top:26px;font-size:84px">25% Off</div>
  <div class="vert" style="left:27px;top:539px;font-size:78px;color:var(--pink-hot)">Mother’s Day</div>
  <div class="vert" style="left:109px;top:539px;font-size:56px">Spring Detox Sale</div>
</section>

<section class="tile t3 col-a row-2">
  <div class="photo" role="img" aria-label="Smiling woman in a white sweater pointing at supplement bottles on a kitchen counter"></div>
  <svg class="shape" width="461" height="575" viewBox="0 0 461 575"><path d="M0 0H332L272 118H0Z" fill="var(--sky)"/></svg>
  <div class="line" style="left:28px;top:32px;font-size:80px">25% Off</div>
  <div class="line" style="left:28px;top:130px;font-size:27px;font-weight:600">All Supplements</div>
  <div class="line" style="left:28px;top:172px;font-size:45px;font-weight:600">Spring Detox</div>
  <div class="vert heavy" style="left:22px;top:532px;font-size:122px;color:var(--sun);font-weight:400">Sale!</div>
</section>

<section class="tile t4 col-b row-2">
  <svg class="shape" width="461" height="575" viewBox="0 0 461 575"><path d="M0 0H461V222C400 250 340 228 260 225C170 222 90 250 0 240Z" fill="var(--crimson)"/></svg>
  <div class="photo" role="img" aria-label="Four supplement bottles lined up on a white surface" style="left:0;top:250px;width:461px;height:170px;background:linear-gradient(180deg,#eeedea,#e0deda)"></div>
  <div class="line center" style="top:24px;font-size:100px">25% Off</div>
  <div class="line center" style="top:150px;font-size:56px">Spring Detox Sale</div>
  <div class="rule" style="left:62px;width:48px"></div>
  <div class="rule" style="left:351px;width:46px"></div>
  <div class="line center" style="top:452px;font-size:42px;color:var(--crimson);font-weight:600">Spring Reset</div>
  <div class="line center" style="top:500px;font-size:60px;color:var(--ink)">Summer Ready</div>
</section>

<section class="tile t5 col-a row-3">
  <div class="photo" role="img" aria-label="Softly faded kitchen scene with supplement bottles in the background"></div>
  <div class="box badge"></div>
  <div class="line center" style="top:52px;font-size:88px;font-weight:600">25% Off</div>
  <div class="line center light" style="top:160px;font-size:52px">Everything</div>
  <div class="line center" style="top:234px;font-size:74px">Mother’s Day</div>
  <div class="line center light" style="top:314px;font-size:76px">Spring Detox</div>
  <div class="line center heavy" style="top:392px;font-size:136px;color:var(--mint)">Sale</div>
</section>

<section class="tile t6 col-b row-3">
  <svg class="shape" width="461" height="575" viewBox="0 0 461 575"><path d="M0 0H461V55C400 140 310 172 230 172C150 172 60 140 0 55Z" fill="var(--plum)"/></svg>
  <div class="line center" style="top:45px;font-size:84px;font-weight:600">25% Off</div>
  <div class="line center" style="top:198px;font-size:76px;font-weight:600">Mother’s Day</div>
  <div class="box frame"></div>
  <div class="line center heavy" style="top:298px;font-size:130px">Sale</div>
  <div class="line center" style="top:458px;font-size:50px">Feel Amazing Again!</div>
</section>

<section class="tile t7 col-a row-4">
  <svg class="shape" width="461" height="575" viewBox="0 0 461 575"><path d="M0 0H461V250C400 262 330 268 250 266C150 262 80 258 0 277Z" fill="var(--white)"/></svg>
  <div class="line center" style="top:42px;font-size:112px;color:var(--navy-text)">25% Off</div>
  <div class="line center" style="top:160px;font-size:78px;color:var(--ink)">Mother’s Day</div>
  <div class="box frame"></div>
  <div class="line center heavy" style="top:330px;font-size:108px;text-transform:none">Sale</div>
  <div class="line center heavy" style="top:467px;font-size:50px;text-transform:none">Refresh Your Body</div>
</section>

<section class="tile t8 col-b row-4">
  <div class="photo" role="img" aria-label="Smiling woman in a white sweater standing behind a row of supplement bottles"></div>
  <div class="box band"></div>
  <div class="line center" style="top:24px;font-size:96px">25% Off</div>
  <div class="line dark" style="left:27px;top:140px;font-size:68px">Spring</div>
  <div class="line dark" style="left:27px;top:215px;font-size:68px">Detox</div>
  <div class="box frame"></div>
  <div class="line" style="left:42px;top:290px;font-size:66px">Sale</div>
  <div class="line dark" style="left:28px;top:376px;font-size:50px">Spring</div>
  <div class="line dark" style="left:28px;top:432px;font-size:36px">Cleanse.</div>
  <div class="line dark" style="left:28px;top:474px;font-size:36px">Summer</div>
  <div class="line dark" style="left:28px;top:514px;font-size:36px">Glow</div>
</section>

<section class="tile t9 col-a row-5">
  <div class="photo" role="img" aria-label="Smiling woman in a white sweater pointing at supplement bottles on a kitchen counter"></div>
  <div class="line" style="top:57px;font-size:78px;font-weight:600">25% Off</div>
  <div class="line" style="top:142px;font-size:48px;font-weight:600">Mother’s Day</div>
  <div class="box frame"></div>
  <div class="line" style="top:210px;font-size:74px;color:var(--ink);font-weight:600">Sale</div>
  <div class="line" style="top:312px;font-size:56px;font-weight:600">Detox</div>
  <div class="line" style="top:366px;font-size:35px;font-weight:600">This Spring.</div>
  <div class="line" style="top:427px;font-size:56px;font-weight:600">Shine</div>
  <div class="line" style="top:486px;font-size:35px;font-weight:600">This Summer</div>
</section>

<section class="tile t10 col-b row-5">
  <svg class="shape" width="461" height="575" viewBox="0 0 461 575"><path d="M0 0H125L0 90Z" fill="var(--maroon)"/><path d="M0 150C70 310 170 430 270 500C340 545 420 562 461 560V575H0Z" fill="var(--maroon)"/></svg>
  <div class="photo" role="img" aria-label="Smiling woman in a white sweater with a row of supplement bottles in front"></div>
  <div class="line" style="right:17px;top:42px;font-size:76px;color:var(--maroon);font-weight:600">Mother’s Day</div>
  <div class="line heavy" style="top:122px;font-size:130px;color:var(--ink)">Sale</div>
  <div class="line" style="top:257px;font-size:58px;color:var(--maroon);font-weight:600">Spring Detox</div>
  <div class="line" style="top:323px;font-size:42px;color:var(--ink);font-weight:600">For A</div>
  <div class="line" style="top:373px;font-size:58px;color:var(--maroon);font-weight:600">Summer</div>
  <div class="line" style="top:445px;font-size:58px;color:var(--maroon);font-weight:600">Body</div>
</section>

</body>
</html>
```